My Pebble Porch Path Blog Re-Do Launch

I need a blog makeover. Someone started for me and they sold their company. The blog is primarily spiritual/inspirational. I would eventually like to monetize and launch some ebooks and/or other products. I am open to suggestions. I am learning as we go along, so please keep that in mind. The final design should be warm and welcoming. I am open to suggestions. I am looking to build a relationship.

Target Market(s)

women, moms, females with chronic health issues, moms of special needs kids, those who need encouragement

Industry/Entity Type

Religious

Number of Pages Required

4 page

Font styles to use
Sans Serif

Colors
eddcec
fdf9cf
ffffff

Requirements
Must have
• I would like my main page to have a short about section, relevant posts, recent posts, and archive posts. The main page should also have a place to subscribe as well a search feature.
Nice to have
• Buttons (grab my button), blogs I follow, e-cart capabilities

```html
<!DOCTYPE html>
<html lang="en">
<head>
<meta charset="utf-8">
<title>My Pebble Porch Path</title>
<link rel="stylesheet" href="https://fonts.googleapis.com/css2?family=Arimo:wght@400;700&family=Tinos:ital,wght@0,400;1,400&display=swap">
<style>
:root{
  --lavender:#ecdaed;
  --lavender-deep:#e4cbe6;
  --lavender-line:#d9bfdc;
  --cream:#fdf9cf;
  --cream-btn:#fbf2b8;
  --white:#ffffff;
  --ink:#333333;
  --text:#5a5a5a;
  --muted:#9a9a9a;
  --rose:#ecbcdc;
  --rule:#e3e3e3;
  --footer:#f4f4f4;
  --sans:'Arimo',Arial,sans-serif;
  --serif:'Tinos','Times New Roman',serif;
}
*{box-sizing:border-box;margin:0;padding:0}
html,body{width:1200px;height:2299px;overflow:hidden;background:var(--white)}
body{position:relative;font-family:var(--sans);color:var(--text)}
.abs{position:absolute}
svg{display:block}

/* header */
.site-header{left:0;top:0;width:1200px;height:141px}
.brand{left:100px;top:38px;display:flex;align-items:center;gap:14px}
.brand-mark{width:52px;height:52px;border-radius:50%;background:var(--lavender-deep)}
.brand-name{font-family:var(--serif);font-size:27px;color:#4a4150;line-height:1.1;width:190px}
.follow{left:720px;top:58px;display:flex;align-items:center;gap:10px;font-size:13px;color:#888}
.social-dot{width:36px;height:36px;border:1px solid #e2e2e2;border-radius:50%}
.follow .label{margin-right:4px}
.cart-link{margin-left:26px;display:flex;align-items:center;gap:10px}
.cart-link .social-dot{display:flex;align-items:center;justify-content:center}

/* nav */
.main-nav{left:0;top:141px;width:1200px;height:58px;border-top:1px solid var(--rule);border-bottom:1px solid var(--rule)}
.nav-item{top:0;height:57px;display:flex;align-items:center;justify-content:center;font-size:11px;color:#555;letter-spacing:.3px}
.nav-item::after{content:"";width:5px;height:5px;border-right:1px solid #777;border-bottom:1px solid #777;transform:rotate(45deg);margin:-3px 0 0 7px}
.nav-item.is-active{background:var(--lavender)}
.nav-divider{left:1060px;top:12px;width:1px;height:34px;background:var(--rule)}
.nav-search{left:1088px;top:20px}

/* hero */
.hero-photo{left:0;top:199px;width:779px;height:517px;background:radial-gradient(ellipse at 30% 55%,#8a7e74 0%,#b7ada4 35%,#ded8d2 70%,#f2efec 100%)}
.hero-story{left:779px;top:199px;width:421px;height:517px;background:var(--lavender)}
.eyebrow{left:22px;top:49px;font-size:12px;color:#555;letter-spacing:.3px}
.hero-title{left:22px;top:70px;width:360px;font-family:var(--serif);font-size:21px;line-height:31px;color:#222;font-weight:400}
.hero-copy{left:22px;top:140px;width:372px;font-size:11.5px;line-height:22px;color:#555}
.btn-cream{background:var(--cream-btn);border-radius:6px;box-shadow:0 2px 3px rgba(0,0,0,.18);font-size:11.5px;color:#444;display:flex;align-items:center;justify-content:center;gap:8px}
.hero-btn{left:22px;top:357px;width:138px;height:45px}
.hero-pager{left:0;top:453px;width:421px;height:64px;background:var(--lavender-deep)}
.pager-btn{top:0;width:72px;height:64px;border-right:1px solid #f3e6f4;display:flex;align-items:center;justify-content:center}

/* section heads */
.section-head{left:98px;width:707px;height:30px;border-bottom:1px solid var(--rule)}
.section-head h2{font-size:22px;font-weight:400;color:#444;line-height:22px}
.mini-arrows{right:0;top:2px;display:flex;gap:4px}
.mini-arrows span{width:16px;height:14px;border:1px solid #ccc;display:flex;align-items:center;justify-content:center}

/* posts */
.photo{border-radius:0}
.post-title{font-size:13.5px;line-height:23px;color:#333}
.post-date{font-size:10.5px;color:var(--rose);display:flex;align-items:center;gap:6px;letter-spacing:.2px}
.post-excerpt{font-size:11.5px;line-height:22px;color:#666}
.action-bar{height:42px;border:1px solid #ecd9ec;display:flex}
.action-bar>div{border-right:1px solid #ecd9ec;display:flex;align-items:center;justify-content:center;gap:7px;font-size:11px;color:var(--rose)}
.action-bar>div:last-child{border-right:none}
.dots{display:flex;gap:12px}
.dots i{width:7px;height:7px;border-radius:50%;background:var(--rose);display:block}

/* sidebar */
.recent{left:842px;top:757px;width:259px;height:531px;background:var(--cream)}
.side-title{font-size:16px;color:#333}
.recent .side-title{left:20px;top:14px}
.recent-item{left:18px;width:223px;height:96px;border-top:1px solid #e9e3b4;display:flex;gap:17px;padding-top:12px}
.recent-thumb{width:66px;height:58px;flex:none}
.recent-text{font-size:11.5px;line-height:19px;color:#333}
.recent-text em{display:block;margin-top:5px;font-family:var(--serif);font-size:10.5px;color:var(--muted)}
.newsletter{left:842px;top:1311px;width:259px;height:191px;background:var(--lavender);text-align:center}
.newsletter .side-title{left:0;top:22px;width:259px}
.news-note{left:20px;top:48px;width:219px;font-family:var(--serif);font-style:italic;font-size:10px;line-height:14px;color:#a895a8}
.news-input{left:14px;top:95px;width:231px;height:31px;background:var(--white);border-radius:3px;font-size:10.5px;color:#888;text-align:left;padding:10px 0 0 12px}
.news-btn{left:14px;top:134px;width:231px;height:32px;font-size:10.5px}
.shop{left:842px;top:1526px;width:259px;height:469px;background:var(--lavender);text-align:center}
.shop-photo{left:0;top:0;width:259px;height:200px;background:linear-gradient(160deg,#a8b39f 0%,#d8d4c6 45%,#8f7a60 75%,#6e6a55 100%)}
.shop .side-title{left:0;top:218px;width:259px;font-size:17px}
.shop-copy{left:16px;top:245px;width:227px;font-size:10.5px;line-height:19px;color:#555}
.shop-btn{left:22px;top:409px;width:215px;height:40px;font-size:11px}

/* footer */
.site-footer{left:0;top:2036px;width:1200px;height:211px;background:var(--footer)}
.foot-col h3{font-size:16px;font-weight:400;color:#333;margin-bottom:16px}
.foot-col li{list-style:none;font-size:11px;line-height:22.5px;color:#444}
.foot-rule{top:28px;width:1px;height:150px;background:#dcdcdc}
.contact-line{display:flex;gap:12px;font-size:11px;line-height:22px;color:#444;margin-bottom:12px}
.contact-line svg{margin-top:5px;flex:none}
.foot-brand{left:868px;top:52px;display:flex;align-items:center;gap:14px}
.legal{left:0;top:2247px;width:1200px;height:52px;background:var(--cream);font-size:11px;color:#333;display:flex;align-items:center;justify-content:center}
</style>
</head>
<body>

<header class="site-header abs">
  <div class="brand abs">
    <span class="brand-mark"></span>
    <span class="brand-name">My Pebble Porch Path</span>
  </div>
  <div class="follow abs">
    <span class="label">Follow With Us:</span>
    <span class="social-dot"></span>
    <span class="social-dot"></span>
    <span class="social-dot"></span>
    <span class="cart-link">E-cart capabilities
      <span class="social-dot">
        <svg width="16" height="14" viewBox="0 0 16 14"><path d="M1 1h3l2 8h8l1.5-5H5" fill="none" stroke="#ccc" stroke-width="1.4"/><circle cx="7" cy="12" r="1.3" fill="#ccc"/><circle cx="13" cy="12" r="1.3" fill="#ccc"/></svg>
      </span>
    </span>
  </div>
</header>

<nav class="main-nav abs">
  <div class="nav-item abs is-active" style="left:98px;width:112px">HOME</div>
  <div class="nav-item abs" style="left:250px;width:110px">ABOUT</div>
  <div class="nav-item abs" style="left:400px;width:130px">FEATURES</div>
  <div class="nav-item abs" style="left:575px;width:160px">RELEVANT POSTS</div>
  <div class="nav-item abs" style="left:770px;width:100px">BLOG</div>
  <div class="nav-item abs" style="left:920px;width:120px">CONTACT</div>
  <div class="nav-divider abs"></div>
  <svg class="nav-search abs" width="16" height="16" viewBox="0 0 16 16"><circle cx="6.5" cy="6.5" r="4.5" fill="none" stroke="#bbb" stroke-width="1.4"/><path d="M10 10l4 4" stroke="#bbb" stroke-width="1.4"/></svg>
</nav>

<section class="hero">
  <div class="hero-photo abs" role="img" aria-label="Sepia photo of hands clasped in prayer"></div>
  <div class="hero-story abs">
    <p class="eyebrow abs">OUR STORY</p>
    <h1 class="hero-title abs">Natus error sit voluptatem aperiam, eaque ipsa quae ab illo invent...</h1>
    <p class="hero-copy abs">Sed quia consequuntur magni dolores eos qui ratione voluptatem sequi nesciunt. Neque porro quisquam est, qui dolorem ipsum quia dolor sit amet, consectetur, adipisci velit, sed quia non numquam eius modi tempora incidunt ut labore et dolore magnam aliquam quaerat voluptatem. Ut enim ad minima veniam, quis nostrum exercitationem ullam corporis suscipit laboriosam, nisi ut aliquid ex ea commodi consequatur? Quis autem vel eum iure reprehenderit qui in ea voluptate velit esse quam nihil molestiae consequatur...</p>
    <div class="hero-btn btn-cream abs">READ MORE INFO!</div>
    <div class="hero-pager abs">
      <div class="pager-btn abs" style="left:0"><svg width="12" height="26" viewBox="0 0 12 26"><path d="M11 1L1 13l10 12" fill="none" stroke="#fff" stroke-width="1.6"/></svg></div>
      <div class="pager-btn abs" style="left:72px"><svg width="12" height="26" viewBox="0 0 12 26"><path d="M1 1l10 12L1 25" fill="none" stroke="#fff" stroke-width="1.6"/></svg></div>
    </div>
  </div>
</section>

<main>
  <div class="section-head abs" style="top:753px">
    <h2>Relevant Posts</h2>
    <div class="mini-arrows abs">
      <span><svg width="6" height="8" viewBox="0 0 6 8"><path d="M5 0L1 4l4 4" fill="none" stroke="#888"/></svg></span>
      <span><svg width="6" height="8" viewBox="0 0 6 8"><path d="M1 0l4 4-4 4" fill="none" stroke="#888"/></svg></span>
    </div>
  </div>

  <article>
    <div class="photo abs" style="left:98px;top:818px;width:707px;height:381px;background:linear-gradient(180deg,#6e1f2e 0%,#c03a2f 35%,#e8683a 65%,#f6b458 85%,#3a1c18 100%)" role="img" aria-label="Silhouette of a person kneeling in prayer beside a cross at sunset"></div>
    <h3 class="post-title abs" style="left:98px;top:1220px;width:680px;font-weight:400">Corporis suscipit laboriosam, nisi ut aliquid ex ea commodi consequatur? Quis autem vel eum iure reprehenderit qui in ea voluptate velit esse quam</h3>
    <p class="post-date abs" style="left:98px;top:1279px"><svg width="10" height="10" viewBox="0 0 10 10"><rect x=".5" y="1.5" width="9" height="8" fill="none" stroke="#ecbcdc"/><path d="M0 4h10" stroke="#ecbcdc"/></svg>24 NOVEMBER 2015</p>
    <p class="post-excerpt abs" style="left:98px;top:1303px;width:707px">Nam libero tempore, cum soluta nobis est eligendi optio cumque nihil impedit quo minus id quod maxime placeat facere possimus, voluptas assumenda est, omnis dolor repellendus. Temporibus autem quibusdam et aut officiis debitis aut rerum necessitatibus saepe eveniet ut et voluptates repudiandae sint et molestiae non recusandae. Itaque earum rerum hic tenetur a sapiente delectus, ut aut reiciendis voluptatibus maiores alias consequatur aut perferendis...</p>
    <div class="action-bar abs" style="left:98px;top:1411px;width:707px">
      <div style="width:157px"><svg width="13" height="11" viewBox="0 0 13 11"><path d="M1 1h11v7H5l-3 2V8H1z" fill="none" stroke="#ecbcdc"/></svg>345_Comments</div>
      <div style="width:156px"><svg width="12" height="11" viewBox="0 0 12 11"><path d="M6 10L1 5a2.6 2.6 0 014-3.3L6 3l1-1.3A2.6 2.6 0 0111 5z" fill="#ecbcdc"/></svg>234_Likes</div>
      <div style="width:156px"><svg width="11" height="11" viewBox="0 0 11 11"><circle cx="2" cy="5.5" r="1.6" fill="#ecbcdc"/><circle cx="9" cy="2" r="1.6" fill="#ecbcdc"/><circle cx="9" cy="9" r="1.6" fill="#ecbcdc"/><path d="M2 5.5L9 2M2 5.5L9 9" stroke="#ecbcdc"/></svg>Share</div>
      <div style="flex:1"><span class="dots"><i></i><i></i><i></i><i></i><i></i></span></div>
    </div>
  </article>

  <div class="section-head abs" style="top:1500px">
    <h2>Archive Posts</h2>
    <div class="mini-arrows abs">
      <span><svg width="6" height="8" viewBox="0 0 6 8"><path d="M5 0L1 4l4 4" fill="none" stroke="#888"/></svg></span>
      <span><svg width="6" height="8" viewBox="0 0 6 8"><path d="M1 0l4 4-4 4" fill="none" stroke="#888"/></svg></span>
    </div>
  </div>

  <article>
    <div class="photo abs" style="left:98px;top:1571px;width:334px;height:196px;background:radial-gradient(ellipse at 50% 55%,#6b5a55 0%,#3f3b3b 55%,#262626 100%)" role="img" aria-label="Woman sitting with hands clasped in prayer"></div>
    <h3 class="post-title abs" style="left:98px;top:1783px;width:334px;font-weight:400">Corporis suscipit laboriosam, nisi ut aliquid ex ea modi consequatur in ea voluptate velit esse quam</h3>
    <p class="post-date abs" style="left:98px;top:1842px"><svg width="10" height="10" viewBox="0 0 10 10"><rect x=".5" y="1.5" width="9" height="8" fill="none" stroke="#ecbcdc"/><path d="M0 4h10" stroke="#ecbcdc"/></svg>24 NOVEMBER 2015</p>
    <p class="post-excerpt abs" style="left:98px;top:1866px;width:334px">Nam libero tempore, cum soluta nobis est eligendi optio cumque nihil dam et aut officiis debitis aut rerum necessitatibus saepe eveniet ut et ibus maiores alias aut perferendis...</p>
    <div class="action-bar abs" style="left:98px;top:1951px;width:334px">
      <div style="width:56px"><svg width="13" height="11" viewBox="0 0 13 11"><path d="M1 1h11v7H5l-3 2V8H1z" fill="#ecbcdc"/></svg></div>
      <div style="width:56px"><svg width="12" height="11" viewBox="0 0 12 11"><path d="M6 10L1 5a2.6 2.6 0 014-3.3L6 3l1-1.3A2.6 2.6 0 0111 5z" fill="#ecbcdc"/></svg></div>
      <div style="width:56px"><svg width="11" height="11" viewBox="0 0 11 11"><circle cx="2" cy="5.5" r="1.6" fill="#ecbcdc"/><circle cx="9" cy="2" r="1.6" fill="#ecbcdc"/><circle cx="9" cy="9" r="1.6" fill="#ecbcdc"/><path d="M2 5.5L9 2M2 5.5L9 9" stroke="#ecbcdc"/></svg></div>
      <div style="flex:1"><span class="dots"><i></i><i></i><i></i><i></i><i></i></span></div>
    </div>
  </article>

  <article>
    <div class="photo abs" style="left:471px;top:1571px;width:334px;height:196px;background:linear-gradient(135deg,#4a4745 0%,#8c7f74 40%,#d9d3cb 75%,#eeeae5 100%)" role="img" aria-label="Hands folded over an open Bible holding a small cross"></div>
    <h3 class="post-title abs" style="left:471px;top:1783px;width:334px;font-weight:400">Corporis suscipit laboriosam, nisi ut aliquid ex ea modi consequatur in ea voluptate velit esse quam</h3>
    <p class="post-date abs" style="left:471px;top:1842px"><svg width="10" height="10" viewBox="0 0 10 10"><rect x=".5" y="1.5" width="9" height="8" fill="none" stroke="#ecbcdc"/><path d="M0 4h10" stroke="#ecbcdc"/></svg>24 NOVEMBER 2015</p>
    <p class="post-excerpt abs" style="left:471px;top:1866px;width:334px">Nam libero tempore, cum soluta nobis est eligendi optio cumque nihil dam et aut officiis debitis aut rerum necessitatibus saepe eveniet ut et ibus maiores alias aut perferendis...</p>
    <div class="action-bar abs" style="left:471px;top:1951px;width:334px">
      <div style="width:56px"><svg width="13" height="11" viewBox="0 0 13 11"><path d="M1 1h11v7H5l-3 2V8H1z" fill="#ecbcdc"/></svg></div>
      <div style="width:56px"><svg width="12" height="11" viewBox="0 0 12 11"><path d="M6 10L1 5a2.6 2.6 0 014-3.3L6 3l1-1.3A2.6 2.6 0 0111 5z" fill="#ecbcdc"/></svg></div>
      <div style="width:56px"><svg width="11" height="11" viewBox="0 0 11 11"><circle cx="2" cy="5.5" r="1.6" fill="#ecbcdc"/><circle cx="9" cy="2" r="1.6" fill="#ecbcdc"/><circle cx="9" cy="9" r="1.6" fill="#ecbcdc"/><path d="M2 5.5L9 2M2 5.5L9 9" stroke="#ecbcdc"/></svg></div>
      <div style="flex:1"><span class="dots"><i></i><i></i><i></i><i></i><i></i></span></div>
    </div>
  </article>
</main>

<aside>
  <section class="recent abs">
    <h2 class="side-title abs" style="font-weight:400">Recent Posts</h2>
    <div class="recent-item abs" style="top:48px"><div class="recent-thumb" style="background:linear-gradient(135deg,#6a5a4c,#b8a58d)" role="img" aria-label="Woman praying"></div><p class="recent-text">But I must explain to you how all this mistaken<em>Posted by 27th Aug, 2015</em></p></div>
    <div class="recent-item abs" style="top:144px"><div class="recent-thumb" style="background:linear-gradient(135deg,#3b6fa6,#c9b8a0)" role="img" aria-label="Person kneeling in prayer"></div><p class="recent-text">But I must explain to you how all this mistaken<em>Posted by 27th Aug, 2015</em></p></div>
    <div class="recent-item abs" style="top:240px"><div class="recent-thumb" style="background:linear-gradient(135deg,#2e5870,#9fc6d4)" role="img" aria-label="Cross against a blue sky"></div><p class="recent-text">But I must explain to you how all this mistaken<em>Posted by 27th Aug, 2015</em></p></div>
    <div class="recent-item abs" style="top:336px"><div class="recent-thumb" style="background:linear-gradient(180deg,#6e5a48,#e0a85a 70%,#2a2018)" role="img" aria-label="Silhouette praying at sunset"></div><p class="recent-text">But I must explain to you how all this mistaken<em>Posted by 27th Aug, 2015</em></p></div>
    <div class="recent-item abs" style="top:432px"><div class="recent-thumb" style="background:linear-gradient(180deg,#6e1f2e,#d9583a 70%,#2a1510)" role="img" aria-label="Cross and praying figure at sunset"></div><p class="recent-text">But I must explain to you how all this mistaken<em>Posted by 27th Aug, 2015</em></p></div>
  </section>

  <section class="newsletter abs">
    <h2 class="side-title abs" style="font-weight:400">News Letter</h2>
    <p class="news-note abs">Lorem ipsum dolor sit amet, cadipiscing elit, sed do eiusmod tempor incididunt ut la</p>
    <div class="news-input abs">Enter your e-mail*</div>
    <div class="news-btn btn-cream abs">SUBSCRIBE</div>
  </section>

  <section class="shop abs">
    <div class="shop-photo abs" role="img" aria-label="Wooden prayer beads resting on an open book"></div>
    <h2 class="side-title abs" style="font-weight:400">e-cart capabilities</h2>
    <p class="shop-copy abs">Beatae vitae dicta sunt explicabo. Nemo enim ipsam voluptatem quia voluptas sit aspernatur magnam aliquam quaerat voluptatem. Ut enim ad minima veniam, quis nostrum exercitationem ullam corporis suscipit laboriosam, nisi ut aliquid ex ea commodi tur aut odit aut quis nostrum Ut enim ad fugit...</p>
    <div class="shop-btn btn-cream abs"><svg width="13" height="11" viewBox="0 0 16 14"><path d="M1 1h3l2 8h8l1.5-5H5" fill="#444" stroke="#444" stroke-width="1.4"/><circle cx="7" cy="12" r="1.4" fill="#444"/><circle cx="13" cy="12" r="1.4" fill="#444"/></svg>ADD TO CART</div>
  </section>
</aside>

<footer class="site-footer abs">
  <div class="foot-col abs" style="left:98px;top:26px">
    <h3>Quick links</h3>
    <ul><li>Home</li><li>About</li><li>Features</li><li>Relevant posts</li><li>Blog</li><li>Contact</li></ul>
  </div>
  <div class="foot-rule abs" style="left:242px"></div>
  <div class="foot-col abs" style="left:288px;top:26px;width:220px">
    <h3>Contact Information</h3>
    <div class="contact-line"><svg width="8" height="11" viewBox="0 0 8 11"><path d="M4 11S0 6 0 4a4 4 0 018 0c0 2-4 7-4 7z" fill="#c9b7cc"/></svg><span>12, Company Name Street name<br>City name-34674</span></div>
    <div class="contact-line"><svg width="10" height="10" viewBox="0 0 10 10"><path d="M2 0l2 3-1 1.5a6 6 0 002.5 2.5L7 6l3 2-1.5 2C4 10 0 6 0 1.5z" fill="#c9b7cc"/></svg><span>Call Us: (+123) 456-789</span></div>
    <div class="contact-line"><svg width="11" height="8" viewBox="0 0 11 8"><rect x=".5" y=".5" width="10" height="7" fill="none" stroke="#c9b7cc"/><path d="M.5 .5l5 4 5-4" fill="none" stroke="#c9b7cc"/></svg><span>hello@pebbleporchpath.example</span></div>
  </div>
  <div class="foot-rule abs" style="left:525px"></div>
  <div class="foot-col abs" style="left:590px;top:26px">
    <h3>More Information</h3>
    <ul><li>Aliquip ex ea commodo consequat</li><li>Neque porro quisquam est</li><li>Magnam aliquam quaerat</li><li>Deserunt mollitia animi</li><li>Molestiae non recusandae</li></ul>
  </div>
  <div class="foot-rule abs" style="left:815px"></div>
  <div class="foot-brand abs">
    <span class="brand-mark"></span>
    <span class="brand-name">My Pebble Porch Path</span>
  </div>
</footer>
<div class="legal abs">© My Pebble Porch Path | Allrights reserved.</div>

</body>
</html>
```